Brindovalle Business cards

Dear team, I need to get the design file to suit it to our team. The focus of the business card is the Automotive Market and the design must be in black colour and the logo must be in glossy black. On the front of the card I need to get the following info:

- Name and Surname
- Title
- eMail
- Phone Number
- Skype account
- domain address

```html
<!DOCTYPE html>
<html lang="en">
<head>
<meta charset="utf-8">
<title>Brindovalle Business Card</title>
<link href="https://fonts.googleapis.com/css2?family=Libre+Franklin:wght@400;700&display=swap" rel="stylesheet">
<style>
  :root {
    --page: #d9d6d1;
    --card: #eeeeec;
    --card-edge: #d2d2d0;
    --brand-red: #e4202b;
    --band-navy: #121a45;
    --ink: #1f1f1f;
    --band-text: #e9e6e1;
  }
  html, body {
    margin: 0;
    padding: 0;
    width: 1200px;
    height: 887px;
    overflow: hidden;
    background: var(--page);
    font-family: "Libre Franklin", Arial, sans-serif;
  }
  .card {
    position: absolute;
    left: 80px;
    top: 162px;
    width: 1040px;
    height: 563px;
    background: var(--card);
    border: 2px solid var(--card-edge);
    border-radius: 22px;
    overflow: hidden;
    box-sizing: border-box;
  }
  .brand {
    position: absolute;
    left: 66px;
    top: 70px;
    display: flex;
    align-items: center;
    gap: 14px;
  }
  .brand-dot {
    width: 46px;
    height: 46px;
    border-radius: 50%;
    background: var(--brand-red);
  }
  .brand-name {
    font-weight: 700;
    font-size: 44px;
    color: var(--brand-red);
    letter-spacing: -0.5px;
  }
  .person {
    position: absolute;
    left: 66px;
    top: 222px;
  }
  .person-name {
    margin: 0;
    font-weight: 700;
    font-size: 39px;
    color: var(--brand-red);
    letter-spacing: 0.5px;
    line-height: 1;
  }
  .person-title {
    margin: 8px 0 0;
    font-size: 23px;
    color: var(--ink);
  }
  .contact-band {
    position: absolute;
    left: 0;
    right: 0;
    top: 324px;
    height: 222px;
    background: var(--band-navy);
  }
  .address {
    position: absolute;
    left: 66px;
    top: 20px;
    margin: 0;
    font-style: normal;
    font-size: 24px;
    line-height: 33px;
    color: var(--band-text);
  }
  .contact-list {
    position: absolute;
    left: 66px;
    top: 106px;
    margin: 0;
    padding: 0;
    list-style: none;
    font-size: 24px;
    line-height: 34px;
    color: var(--band-text);
  }
  .contact-list li {
    display: flex;
    align-items: center;
    gap: 6px;
  }
  .contact-list svg {
    width: 18px;
    height: 18px;
    flex: none;
  }
  .emblem {
    position: absolute;
    left: 740px;
    top: 330px;
    width: 220px;
    height: 220px;
    border-radius: 50%;
    background: var(--brand-red);
    border: 6px solid var(--card);
    box-sizing: border-box;
  }
</style>
</head>
<body>
  <div class="card">
    <div class="brand">
      <span class="brand-dot"></span>
      <span class="brand-name">Brindovalle.com</span>
    </div>

    <div class="person">
      <h1 class="person-name">MARCO ALDINI</h1>
      <p class="person-title">Director</p>
    </div>

    <div class="contact-band">
      <address class="address">4120 N Linden, Harlow,<br>Oklahoma 74390</address>
      <ul class="contact-list">
        <li>
          <svg viewBox="0 0 24 24" aria-hidden="true"><path fill="#e4202b" d="M6.6 10.8a15.1 15.1 0 0 0 6.6 6.6l2.2-2.2c.3-.3.7-.4 1-.2 1.1.4 2.3.6 3.6.6.6 0 1 .4 1 1V20c0 .6-.4 1-1 1A17 17 0 0 1 3 4c0-.6.4-1 1-1h3.5c.6 0 1 .4 1 1 0 1.3.2 2.5.6 3.6.1.3 0 .7-.2 1z"/></svg>
          555-014-2287
        </li>
        <li>
          <svg viewBox="0 0 24 24" aria-hidden="true"><rect x="2" y="5" width="20" height="14" rx="1.5" fill="#e4202b"/><path d="M3 6l9 7 9-7" stroke="#121a45" stroke-width="1.6" fill="none"/></svg>
          info@brindovalle.com
        </li>
        <li>
          <svg viewBox="0 0 24 24" aria-hidden="true"><circle cx="12" cy="12" r="9" fill="#e4202b"/></svg>
          brindovalle
        </li>
      </ul>
    </div>

    <div class="emblem"></div>
  </div>
</body>
</html>
```